Business card design needed

Family General Practitioner/ Family Physician.
Logo is the logo of the Noble Guild of Family Healers Oceania
http://kpltw.varendo.example/ImageShelf/marks/pages/NGFHO%20mark_jpg.htm
Updates

Project Deadline Extended
Reason: Just a bit more time to make changes and the weekend for me to look at things closely and to choose. Thanks, Orin

Thanks for all the submissions. So many of them are really works of art. Not one of them are not good. The ones that I am eliminating are the ones that I think are not suitable for me personally only, and because if I don't, it makes it very difficult to decide as many of you are also sending me slight variations of a card. I have just decided to choose a second place card too. Can't thank you all enough. Good luck, Orin. P.S - Working today till 10 pm as the card says :-), so probably won't be able to give a feedback till late Saturday night or Sunday morning here in Sydney, Australia. 

Project Deadline Extended
Reason: Just added a second place to the budget and realised that Australia is ahead of the rest of the world in the time zone (only :-) - don't want to offend anyone or start a debate!! ) , so Monday deadline will mean it will be a weekend for the rest of the world. Just wanted to give everyone more time to submit their best, especially since I will be picking a second card too. Can't thank everyone enough for the submissions. P.S - Not keen on photos on the card.

Industry/Entity Type

Business

Contact Information for Business Card

Dr. Orin Halvey M.B.B.S., F.N.G.F.H.O
Family General Practitioner
Address, timings, phone and fax number on the back.

Requirements
Must have
• Timings
Mon 7 am - 7 pm
Tues 7 am - 12 pm
Wed 7 am - 10 pm
Thurs 7 am - 12 pm
Fri 7 am - 8 pm
Sat 8 am - 10 pm
Sun - Off

```html
<!DOCTYPE html>
<html lang="en">
<head>
<meta charset="utf-8">
<title>Dr. Orin Halvey – Business Card Options</title>
<link href="https://fonts.googleapis.com/css2?family=Cinzel:wght@400;500&family=Tinos:wght@400;700&family=Open+Sans:wght@400;700&family=Arimo:wght@700&display=swap" rel="stylesheet">
<style>
  :root {
    --backdrop: #d9d4ce;
    --blue-light: #1fa3dc;
    --blue-deep: #1c6cb6;
    --plum: #2f1b35;
    --white: #ffffff;
    --accent-orange: #f0a021;
    --accent-silver: #c9ccd2;
    --accent-sky: #5cc6ee;
    --rule: #9cc63e;
    --crest-faint: rgba(255,255,255,0.10);
  }
  * { box-sizing: border-box; margin: 0; padding: 0; }
  html, body { width: 1200px; height: 739px; overflow: hidden; }
  body { background: var(--backdrop); position: relative; font-family: "Open Sans", sans-serif; color: var(--white); }

  .card {
    position: absolute; overflow: hidden;
    background: linear-gradient(120deg, var(--blue-light) 0%, var(--blue-deep) 100%);
    box-shadow: 0 2px 6px rgba(0,0,0,0.35);
  }

  /* Front */
  .card--front { left: 35px; top: 27px; width: 525px; height: 300px; }
  .card--front .wave { position: absolute; left: 0; top: 0; width: 525px; height: 300px; }
  .doctor-name {
    position: absolute; left: 0; width: 525px; top: 46px; text-align: center;
    font-family: "Cinzel", serif; font-size: 38px; letter-spacing: 1px; font-weight: 400;
  }
  .doctor-name .cap { font-size: 44px; }
  .credentials {
    position: absolute; left: 0; width: 525px; top: 98px; text-align: center;
    font-family: "Tinos", serif; font-size: 11px; letter-spacing: 0.5px;
  }
  .specialty {
    position: absolute; left: 0; width: 525px; top: 143px; text-align: center;
    font-family: "Tinos", serif; font-size: 19px; letter-spacing: 2.4px;
  }
  .tagline {
    position: absolute; left: 122px; top: 256px;
    font-family: "Tinos", serif; font-weight: 700; font-size: 22px;
  }
  .college-mark {
    position: absolute; left: 420px; top: 208px; width: 96px;
    display: flex; flex-direction: column; align-items: center; gap: 5px;
    font-family: "Tinos", serif; font-size: 10px; line-height: 1.2; text-align: center; color: var(--white);
  }
  .college-mark .dot { width: 26px; height: 26px; border-radius: 50%; background: var(--white); }

  /* Backs */
  .card--back { width: 526px; height: 300px; }
  .card--opt1 { left: 615px; top: 27px; }
  .card--opt2 { left: 47px; top: 368px; }
  .card--opt3 { left: 611px; top: 376px; }

  .college-watermark {
    position: absolute; right: 40px; top: 50px; width: 190px; height: 160px;
    display: flex; flex-direction: column; align-items: center; justify-content: center; gap: 8px;
    font-family: "Tinos", serif; font-size: 17px; line-height: 1.25; text-align: center; color: var(--crest-faint);
  }
  .college-watermark .dot { width: 52px; height: 52px; border-radius: 50%; background: var(--crest-faint); }

  .hours-title { position: absolute; font-size: 20px; font-weight: 400; letter-spacing: 0.3px; }
  .hours { position: absolute; list-style: none; font-size: 16px; line-height: 23px; }
  .hours b { font-weight: 700; }
  .card--opt1 .hours-title { left: 38px; top: 15px; }
  .card--opt1 .hours { left: 38px; top: 45px; font-weight: 700; text-transform: uppercase; }
  .card--opt1 .hours li span { margin-right: 8px; }

  .card--opt2 .hours-title { left: 50px; top: 6px; letter-spacing: 1.2px; }
  .card--opt2 .hours { left: 31px; top: 41px; line-height: 23.8px; }
  .card--opt2 .hours li { display: flex; }
  .card--opt2 .hours li span { width: 110px; }

  .card--opt3 .hours-title { left: 38px; top: 15px; }
  .card--opt3 .hours { left: 38px; top: 45px; }
  .card--opt3 .hours li span { margin-right: 6px; }

  .contact-band {
    position: absolute; left: 0; bottom: 0; width: 100%; height: 80px;
    background: var(--plum); border-top: 2px solid var(--rule);
    font-family: "Tinos", serif; font-size: 15px; line-height: 19px; text-align: center; padding-top: 10px;
  }
  .contact-band .phones { margin-top: 8px; }
  .contact-band .sep { display: inline-block; width: 1px; height: 17px; background: var(--white); vertical-align: -3px; margin: 0 7px; }

  .option-label {
    position: absolute; font-family: "Arimo", sans-serif; font-weight: 700; font-size: 20px;
    color: var(--white); text-shadow: 1px 1px 0 #3a2414, -1px -1px 0 #3a2414, 1px -1px 0 #3a2414, -1px 1px 0 #3a2414;
  }
</style>
</head>
<body>

<section class="card card--front">
  <svg class="wave" viewBox="0 0 525 300" aria-hidden="true">
    <path d="M0 190 C 80 260, 200 250, 300 225 C 380 205, 450 200, 525 205 L525 300 L0 300 Z" fill="var(--plum)"/>
    <path d="M0 170 C 60 235, 180 240, 300 212 C 380 194, 450 188, 525 192" fill="none" stroke="var(--accent-orange)" stroke-width="7"/>
    <path d="M0 182 C 70 246, 190 246, 300 219 C 380 200, 450 194, 525 198" fill="none" stroke="var(--accent-silver)" stroke-width="5"/>
    <path d="M0 191 C 80 256, 200 252, 300 226 C 380 206, 450 200, 525 204" fill="none" stroke="var(--accent-sky)" stroke-width="4"/>
  </svg>
  <h1 class="doctor-name"><span class="cap">D</span>R. <span class="cap">O</span>RIN <span class="cap">H</span>ALVEY</h1>
  <p class="credentials">M.B.B.S., F.N.G.F.H.O</p>
  <p class="specialty">Family General Practitioner</p>
  <p class="tagline">Caring about your health</p>
  <div class="college-mark"><span class="dot"></span>Noble Guild of Family Healers Oceania</div>
</section>

<section class="card card--back card--opt1">
  <div class="college-watermark"><span class="dot"></span>Noble Guild of Family Healers Oceania</div>
  <h2 class="hours-title">Working Hours</h2>
  <ul class="hours">
    <li><span>Monday</span> 7 AM&nbsp;&nbsp;- 7 PM</li>
    <li><span>Tuesday</span>7 AM - 12 PM</li>
    <li><span>Wednesday</span>7 AM - 10 PM</li>
    <li><span>Thursday</span>7 AM - 12 PM</li>
    <li><span>Friday</span>&nbsp; 7 AM&nbsp;&nbsp;- 8 PM</li>
    <li><span>Saturday</span>8 AM - 10 PM</li>
    <li>Sunday - Off</li>
  </ul>
  <footer class="contact-band">
    <p>Upper Level, Linden Court, Harrowgate Shopping Centre<br>Fernbrook Hill, NSW 2199</p>
    <p class="phones">P: 02 5550 1840<span class="sep"></span>F: 02 5550 1862</p>
  </footer>
</section>
<p class="option-label" style="left:822px; top:340px;">Option# 1</p>

<section class="card card--back card--opt2">
  <div class="college-watermark"><span class="dot"></span>Noble Guild of Family Healers Oceania</div>
  <h2 class="hours-title">Working Hours</h2>
  <ul class="hours">
    <li><span>Monday</span><b>7 AM&nbsp;&nbsp;- 7 PM</b></li>
    <li><span>Tuesday</span><b>7 AM - 12 PM</b></li>
    <li><span>Wednesday</span><b>7 AM - 10 PM</b></li>
    <li><span>Thursday</span><b>7 AM - 12 PM</b></li>
    <li><span>Friday</span><b>7 AM&nbsp;&nbsp;- 8 PM</b></li>
    <li><span>Saturday</span><b>8 AM - 10 PM</b></li>
    <li><span>Sunday</span><b>OFF</b></li>
  </ul>
  <footer class="contact-band">
    <p>Upper Level, Linden Court, Harrowgate Shopping Centre<br>Fernbrook Hill, NSW 2199</p>
    <p class="phones">P: 02 5550 1840<span class="sep"></span>F: 02 5550 1862</p>
  </footer>
</section>
<p class="option-label" style="left:254px; top:681px;">Option# 2</p>

<section class="card card--back card--opt3">
  <div class="college-watermark"><span class="dot"></span>Noble Guild of Family Healers Oceania</div>
  <h2 class="hours-title">Working Hours</h2>
  <ul class="hours">
    <li><span>Monday</span><b>7 AM&nbsp;&nbsp;- 7 PM</b></li>
    <li><span>Tuesday</span><b>7 AM - 12 PM</b></li>
    <li><span>Wednesday</span><b>7 AM - 10 PM</b></li>
    <li><span>Thursday</span><b>7 AM - 12 PM</b></li>
    <li><span>Friday</span>&nbsp;&nbsp;<b>7 AM&nbsp;&nbsp;- 8 PM</b></li>
    <li><span>Saturday</span><b>8 AM - 10 PM</b></li>
    <li>Sunday - <b>OFF</b></li>
  </ul>
  <footer class="contact-band">
    <p>Upper Level, Linden Court, Harrowgate Shopping Centre<br>Fernbrook Hill, NSW 2199</p>
    <p class="phones">P: 02 5550 1840<span class="sep"></span>F: 02 5550 1862</p>
  </footer>
</section>
<p class="option-label" style="left:819px; top:689px;">Option# 3</p>

</body>
</html>
```